** Wanted ** Wordpress web design for scaffolding rental and construction company

We need a website design and must be functional to show a basic overview of what our company offers as a service. We have a domain name and a logo but we need web design. This web site should have another scaffolding rental page for construction and renovation as well as a quote section where customers can enter their personal information and also upload photos. The site% 26quot; www.brindlework.com% 26quot; should be intuitive, clear and classy ... The logo must be found on the site in several ways.

Target Market(s)

Professional and no professional

Coding

Coded - Design and coding required

Number of Pages Required

3 page

Font styles to use
Serif
Sans Serif
Decorative
Script

Requirements
Must have
• Our logo
Nice to have
• Slogan:% 26quot; The height% 26 # 224; port% 26 # 233; e hand% 26quot;

```html
<!DOCTYPE html>
<html lang="en">
<head>
<meta charset="utf-8">
<title>Brindlework – Construction</title>
<link href="https://fonts.googleapis.com/css2?family=Poppins:wght@300;400;500;600;700&display=swap" rel="stylesheet">
<style>
:root{
  --orange:#ef8422;
  --black:#000;
  --white:#fff;
  --ink:#222;
  --grey:#666;
  --rule:#555;
}
*{margin:0;padding:0;box-sizing:border-box}
html,body{width:1200px;height:2241px;overflow:hidden;background:var(--white)}
body{position:relative;font-family:'Poppins',sans-serif;color:var(--ink)}
.abs{position:absolute}

/* top bar */
.topbar{left:0;top:0;width:1200px;height:125px;background:var(--black)}
.brand{left:111px;top:70px;width:172px;height:36px;border:3px solid var(--orange);color:var(--white);font-weight:700;font-size:16px;letter-spacing:1px;display:flex;align-items:center;justify-content:center}
.brand-square{left:183px;top:18px;width:28px;height:28px;background:var(--orange)}
.contact-label{color:var(--white);font-size:17px;font-weight:300}
.contact-value{color:var(--orange);font-size:21px;font-weight:600}
.lang{left:976px;top:40px;width:111px;height:46px;border:2px solid var(--white);display:flex;align-items:center;padding-left:5px;gap:8px;color:var(--white);font-weight:600;font-size:17px}
.lang-chip{width:42px;height:30px;background:#2b3f8c}

/* nav */
.nav{left:0;top:125px;width:1200px;height:78px;display:flex;align-items:center}
.nav a{position:absolute;color:var(--ink);text-decoration:none;font-size:17px;font-weight:400}

/* hero */
.hero{left:0;top:203px;width:1200px;height:309px;background:linear-gradient(180deg,#5a5670 0%,#7b6a80 45%,#b77f6f 80%,#cf7c4d 100%)}
.hero-photo{left:590px;top:203px;width:610px;height:309px;background:linear-gradient(180deg,#3a3a4c 0%,#2a2a36 60%,#403036 100%);opacity:.85}
.hero h1{left:109px;top:287px;color:var(--white);font-size:42px;font-weight:600}
.hero-text{left:110px;top:355px;width:560px;color:var(--white);font-size:16px;line-height:26px}

/* about */
.about-frame{left:146px;top:625px;width:355px;height:380px;border:5px solid var(--orange)}
.about-photo{left:111px;top:591px;width:355px;height:379px;background:linear-gradient(135deg,#3a7fb5 0%,#8fb2cc 40%,#e0892f 70%,#6b5a48 100%)}
.about-mark{left:543px;top:620px;width:64px;height:64px;background:var(--orange)}
.about-kicker{left:621px;top:614px;font-size:22px;font-weight:300;color:var(--ink)}
.about-title{left:621px;top:643px;font-size:34px;font-weight:700;color:var(--orange);letter-spacing:.5px}
.about-copy{left:541px;top:710px;width:546px;font-size:14px;line-height:23px;color:var(--grey);text-align:justify}
.about-copy p{margin-bottom:12px}
.intro{left:111px;top:1050px;width:978px;font-size:14.3px;line-height:30px;text-align:center;color:var(--ink)}
.intro p{margin-bottom:13px}

/* diamonds */
.gallery{left:0;top:1260px;width:1200px;height:400px}

/* signup */
.signup{left:0;top:1736px;width:1200px;height:103px;background:var(--orange)}
.signup h2{left:111px;top:1766px;color:var(--white);font-size:28px;font-weight:600}
.field{left:524px;top:1761px;width:392px;height:54px;background:var(--white);font-size:15px;color:#555;padding-left:12px;display:flex;align-items:center}
.send{left:927px;top:1761px;width:160px;height:54px;border:2px solid var(--white);color:var(--white);font-weight:600;font-size:17px;display:flex;align-items:center;justify-content:center}

/* footer */
.footer{left:0;top:1839px;width:1200px;height:402px;background:var(--black)}
.foot-brand{left:113px;top:2011px;width:297px;height:58px;border:3px solid var(--orange);color:var(--white);font-size:26px;font-weight:700;letter-spacing:2px;display:flex;align-items:center;justify-content:center}
.foot-square{left:226px;top:1920px;width:72px;height:72px;background:var(--orange)}
.foot-col h3{color:var(--white);font-size:25px;font-weight:700;margin-bottom:8px;letter-spacing:-.3px}
.foot-col li{list-style:none;color:var(--white);font-size:18px;font-weight:300;line-height:26.5px}
.foot-col li::before{content:">";margin-right:14px}
.social{display:flex;align-items:center;gap:12px;color:var(--white);font-size:20px;font-weight:500;margin-top:16px}
.social span.ring{width:46px;height:46px;border:2px solid var(--white);border-radius:50%;display:inline-block}
.foot-rule{left:111px;top:2145px;width:978px;height:2px;background:var(--rule)}
.copyright{left:0;top:2182px;width:1200px;text-align:center;color:var(--white);font-size:16px;font-weight:500}
</style>
</head>
<body>

<div class="abs topbar"></div>
<div class="abs brand-square"></div>
<div class="abs brand">BRINDLEWORK</div>

<svg class="abs" style="left:411px;top:40px" width="44" height="44" viewBox="0 0 44 44" fill="none" stroke="#fff" stroke-width="2.4" stroke-linecap="round" stroke-linejoin="round">
  <path d="M8 6l7 1 3 9-5 4c3 6 7 10 13 13l4-5 9 3 1 7c-1 2-3 3-5 3C19 40 4 25 4 11c0-2 2-4 4-5z"/>
  <path d="M26 4c7 1 13 7 14 14M26 10c4 1 7 4 8 8"/>
</svg>
<div class="abs contact-label" style="left:466px;top:34px">Call Us At:</div>
<div class="abs contact-value" style="left:466px;top:60px">(555)014-22-90</div>

<svg class="abs" style="left:662px;top:34px" width="32" height="54" viewBox="0 0 32 54" fill="none" stroke="#fff" stroke-width="3">
  <rect x="2" y="2" width="28" height="50" rx="4"/>
  <rect x="7" y="17" width="18" height="13" stroke-width="2"/>
  <path d="M7 17l9 7 9-7" stroke-width="2"/>
  <circle cx="16" cy="45" r="2" fill="#fff" stroke="none"/>
</svg>
<div class="abs contact-label" style="left:709px;top:34px">Email Us At:</div>
<div class="abs contact-value" style="left:709px;top:60px">info@brindlework.com</div>

<div class="abs lang"><span class="lang-chip"></span>Eng <span style="font-size:11px">▼</span></div>

<nav class="abs nav">
  <a style="left:248px">HOME</a>
  <a style="left:395px">ABOUT US</a>
  <a style="left:557px">SERVICES</a>
  <a style="left:715px">GALLERY</a>
  <a style="left:870px">CONTACT US</a>
</nav>

<section>
  <div class="abs hero"></div>
  <div class="abs hero-photo" role="img" aria-label="Silhouettes of workers on scaffolding against an evening sky"></div>
  <div class="hero">
    <h1 class="abs" style="left:109px;top:287px">Construction</h1>
  </div>
  <p class="abs hero-text">Nemo enim ipsam voluptatem quia voluptas sit aspernatur aut odit aut fugit, sed quia consequuntur magnis.</p>
</section>

<section>
  <div class="abs about-frame"></div>
  <div class="abs about-photo" role="img" aria-label="Worker in hard hat and safety vest climbing scaffolding"></div>
  <div class="abs about-mark"></div>
  <div class="abs about-kicker">About</div>
  <div class="abs about-title">CONSTRUCTION</div>
  <div class="abs about-copy">
    <p>Nemo enim ipsam voluptatem quia voluptas sit aspernatur aut odit aut fugit, sed quia consequuntur magni dolores eos qui ratione voluptatem sequi nesciunt. Neque porro quisquam est, qui dolorem ipsum quia dolor sit amet, consectetur, adipisci velit, sed quia non numquam eius modi tempora incidunt ut labore et dolore magnam aliquam quaerat voluptatem.</p>
    <p>Lorem ipsum dolor sit amet, consectetur adipiscing elit. Praesent molestie nec nisl eget scelerisque. Quisque placerat suscipit eros, eu tincidunt tellus blandit vel. molestie nec nisl eget scelerisque.</p>
    <p>Lorem ipsum dolor sit amet, consectetur adipiscing elit. Praesent molestie nec nisl eget scelerisque. Quisque placerat suscipit eros, eu tincidunt tellus blandit vel. molestie nec nisl eget scelerisque.</p>
  </div>
  <div class="abs intro">
    <p>Nemo enim ipsam voluptatem quia voluptas sit aspernatur aut odit aut fugit, sed quia consequuntur magni dolores eos qui ratione voluptatem sequi nesciunt. Neque porro quisquam est, qui dolorem ipsum quia dolor sit amet, consectetur, adipisci velit, sed quia non numquam eius modi tempora incidunt ut laborem.</p>
    <p>Neque porro quisquam est, qui dolorem ipsum quia dolor sit amet, consectetur, adipisci velit, sed quia non numquam eius modi tempora inci dunt ut laborem.</p>
  </div>
</section>

<svg class="abs gallery" width="1200" height="400" viewBox="0 1260 1200 400">
  <defs>
    <filter id="lift" x="-20%" y="-20%" width="140%" height="140%"><feDropShadow dx="0" dy="3" stdDeviation="4" flood-opacity=".25"/></filter>
    <linearGradient id="g1" x1="0" y1="0" x2="1" y2="1"><stop offset="0" stop-color="#c9a27a"/><stop offset=".5" stop-color="#d9df6a"/><stop offset="1" stop-color="#e9e6e2"/></linearGradient>
    <linearGradient id="g2" x1="0" y1="0" x2="0" y2="1"><stop offset="0" stop-color="#3c4c66"/><stop offset=".6" stop-color="#8a8a92"/><stop offset="1" stop-color="#e8a063"/></linearGradient>
    <linearGradient id="g3" x1="0" y1="0" x2="0" y2="1"><stop offset="0" stop-color="#e6e4ea"/><stop offset=".5" stop-color="#7d8fb0"/><stop offset="1" stop-color="#3b3f48"/></linearGradient>
  </defs>
  <g filter="url(#lift)">
    <polygon points="305,1272 493,1460 305,1648 117,1460" fill="#fff"/>
    <polygon points="600,1272 788,1460 600,1648 412,1460" fill="#fff"/>
    <polygon points="896,1272 1084,1460 896,1648 708,1460" fill="#fff"/>
  </g>
  <polygon role="img" aria-label="Engineer in safety vest reviewing plans" points="305,1278 487,1460 305,1642 123,1460" fill="url(#g1)"/>
  <polygon role="img" aria-label="Construction team in hard hats with a laptop" points="600,1278 782,1460 600,1642 418,1460" fill="url(#g2)"/>
  <polygon role="img" aria-label="Two site managers pointing at a building site" points="896,1278 1078,1460 896,1642 714,1460" fill="url(#g3)"/>
</svg>

<section>
  <div class="abs signup"></div>
  <h2 class="abs" style="left:111px;top:1766px;color:#fff;font-size:28px;font-weight:600">Sign Up to get Latest Updates</h2>
  <div class="abs field">Email Address</div>
  <div class="abs send">Send Request</div>
</section>

<footer>
  <div class="abs footer"></div>
  <div class="abs foot-square"></div>
  <div class="abs foot-brand">BRINDLEWORK</div>

  <div class="abs foot-col" style="left:467px;top:1910px">
    <h3>QUICK LINKS</h3>
    <ul><li>Home</li><li>About Us</li><li>Services</li><li>Gallery</li><li>Contact Us</li></ul>
  </div>
  <div class="abs foot-col" style="left:670px;top:1910px">
    <h3>USEFUL LINKS</h3>
    <ul><li>Privacy Policy</li><li>Help Center</li><li>Quotation</li><li>Contact</li><li>General Conditions</li></ul>
  </div>
  <div class="abs foot-col" style="left:910px;top:1910px">
    <h3>SOCIAL MEDIA</h3>
    <div class="social"><span class="ring"></span>Our Page</div>
  </div>

  <div class="abs foot-rule"></div>
  <div class="abs copyright">Copyrights @ 2020 Brindlework. All Rights Reserved.</div>
</footer>

</body>
</html>
```